MBR - Stationery Design Project

We need stationery based on our logo.

Company info :
Cabinet Voisard & Associés
Société à responsabilité limitée au capital de 200.000 FCFP
RCS Papeete 27586K - Numéro tahiti K73962
Centre d’affaires OPALE - Rue Gaston Perrin
BP 61384 MAHU POTE - 98752 Papeete
Tahiti - Polynésie française
Tél : +689 40 73 16 48
Fax : +689 40 39 64 91

Industry/Entity Type

It Company

Font styles to use
Sans Serif

```html
<!DOCTYPE html>
<html lang="fr">
<head>
<meta charset="UTF-8">
<title>MBR – Cartes de visite</title>
<link rel="stylesheet" href="https://fonts.googleapis.com/css2?family=Jost:wght@400;500;700&display=swap">
<style>
  :root {
    --backdrop: #2b2d30;
    --navy: #1d4a7c;
    --navy-deep: #1a3866;
    --navy-dark: #152d55;
    --slate: #8fa3a5;
    --paper: #f7f7f5;
    --ink: #5b5f63;
    --white: #f2f4f6;
  }
  * { margin: 0; padding: 0; box-sizing: border-box; }
  html, body {
    width: 1200px; height: 900px; overflow: hidden;
    background: var(--backdrop);
    font-family: "Jost", "Century Gothic", sans-serif;
  }
  .canvas { position: relative; width: 1200px; height: 900px; }

  .card {
    position: absolute;
    width: 640px; height: 390px;
    overflow: hidden;
    box-shadow: 0 18px 40px rgba(0,0,0,0.45);
  }

  /* Back of card */
  .card--back {
    left: 60px; top: 50px;
    background: linear-gradient(160deg, var(--navy-deep), var(--navy-dark));
    display: flex; align-items: center; justify-content: center;
  }
  .lockup { display: flex; flex-direction: column; align-items: flex-start; }
  .lockup__mark { display: flex; align-items: center; gap: 14px; }
  .lockup__name {
    font-weight: 400; font-size: 108px; line-height: 1;
    letter-spacing: 6px;
  }
  .lockup__square { width: 22px; height: 22px; }
  .lockup__company { font-size: 24px; font-weight: 400; margin-top: 6px; }
  .lockup__services { font-size: 11px; letter-spacing: 0.5px; margin-top: 2px; align-self: flex-end; }

  .card--back .lockup__name,
  .card--back .lockup__company,
  .card--back .lockup__services { color: var(--white); }
  .card--back .lockup__square { background: var(--slate); }

  /* Front of card */
  .card--front { left: 500px; top: 470px; height: 390px; background: var(--paper); }
  .card--front .lockup { position: absolute; right: 44px; top: 40px; }
  .card--front .lockup__name { font-size: 92px; color: var(--navy); }
  .card--front .lockup__square { background: var(--slate); width: 18px; height: 18px; }
  .card--front .lockup__company { font-size: 21px; color: var(--navy); }
  .card--front .lockup__services { font-size: 10px; color: var(--ink); }

  .holder { position: absolute; left: 44px; top: 100px; }
  .holder__name { font-weight: 700; font-size: 22px; letter-spacing: 1px; color: var(--navy); }
  .holder__role { font-size: 18px; color: var(--ink); margin-top: 2px; }

  .contact {
    position: absolute; left: 44px; bottom: 44px;
    font-size: 12.5px; line-height: 1.45; color: var(--ink);
  }
  .contact__label { font-weight: 700; color: var(--navy); }

  .band { position: absolute; bottom: 0; }
  .band--navy { left: 0; width: 62%; height: 12px; background: var(--navy); }
  .band--slate { left: 62%; right: 0; height: 22px; background: var(--slate); }
</style>
</head>
<body>
<main class="canvas">

  <section class="card card--back">
    <div class="lockup">
      <div class="lockup__mark">
        <span class="lockup__name">MBR</span>
        <span class="lockup__square"></span>
      </div>
      <span class="lockup__company">Cabinet Voisard &amp; Associés</span>
      <span class="lockup__services">Expertise-comptable · Audit · Conseil</span>
    </div>
  </section>

  <section class="card card--front">
    <div class="holder">
      <p class="holder__name">LÉA MARCHAND</p>
      <p class="holder__role">Managing Director</p>
    </div>

    <div class="lockup">
      <div class="lockup__mark">
        <span class="lockup__name">MBR</span>
        <span class="lockup__square"></span>
      </div>
      <span class="lockup__company">Cabinet Voisard &amp; Associés</span>
      <span class="lockup__services">Expertise-comptable · Audit · Conseil</span>
    </div>

    <address class="contact" style="font-style: normal;">
      Centre d’affaires OPALE - Rue Gaston Perrin, BP 61384, MAHU POTE - 98752 Papeete<br>
      Tahiti - Polynésie française · <span class="contact__label">Tél:</span> +689 40 73 16 48 · <span class="contact__label">Fax:</span> +689 40 39 64 91
    </address>

    <div class="band band--navy"></div>
    <div class="band band--slate"></div>
  </section>

</main>
</body>
</html>
```